New powerpoint template needed for sales deck using current branding

We need a new PowerPoint template that gives us a fresh modern look and feel without a complete re-brand. We do not want to change our logo or colour scheme however want would like to use them in a different way. Currently our template uses a lot of block colour and we would like to utilise more white with our colour scheme acting as accent colours.

I tried to have a gradient created using our colours but I wasn't happy with the execution - ideally I would be looking for a diagonal gradient adding in some white to offset the brightness of the pink I would also like to see the gradient used translucent over imagery.

I am attaching a template that we currently use that we would like to see updated but also we are looking for some added template pages for graphs, data quotes etc... to help us create an extensive sales deck.

Also attached is a couple of examples from a previous employer that I feel is the look we should aim for in regard to accent colours, layout and the gradient (do not replicate the colours).

I have also attached our brand guidelines.

Hospitality

Other font styles liked:
• Sora

Requirements
Must have
• A full suite of slides usually seen in a sales deck: 2 column pages, data point templates, graphical templates, ability to add imagery
Nice to have
• It would be nice to see different title pages to use including a gradient
Should not have
• colours not featured in our branding - guideline included

```html
<!DOCTYPE html>
<html lang="en">
<head>
<meta charset="utf-8">
<title>Norvel Presentation Template</title>
<link href="https://fonts.googleapis.com/css2?family=Sora:wght@300;400;500;600;700&display=swap" rel="stylesheet">
<style>
  :root{
    --canvas:#ebe1ef;
    --plum:#3d2a4f;
    --ink:#26192f;
    --accent:#5a3c70;
    --pink:#f0648a;
    --muted:#6b6273;
    --rule:#4a3a58;
    --white:#ffffff;
  }
  *{box-sizing:border-box;margin:0;padding:0}
  html,body{width:1200px;height:701px;overflow:hidden;background:var(--canvas)}
  body{position:relative;font-family:"Sora",sans-serif;color:var(--ink)}
  .slide{position:absolute;width:363px;height:202px;overflow:hidden;background:var(--white)}
  .slide > *{position:absolute}
  .col-1{left:44px}.col-2{left:418px}.col-3{left:793px}
  .row-1{top:34px}.row-2{top:249px}.row-3{top:464px}

  .photo-dark{inset:0;background:linear-gradient(135deg,#2f2238 0%,#211827 45%,#2e1b36 100%)}
  .photo-dark.keys{background:linear-gradient(120deg,#261c2e 0%,#1d1623 50%,#2c1b34 100%)}

  .brand{font-weight:500;letter-spacing:-.3px;white-space:nowrap;line-height:1}
  .center{left:0;right:0;text-align:center}
  .light{color:var(--white)}
  .title{font-weight:700;font-size:12px;line-height:1}
  .subtitle{font-weight:400;font-size:7px;line-height:1}
  .presenter{font-weight:600;font-size:7.6px;line-height:1}
  .presenter .hl{color:var(--pink)}
  .meta{font-size:5.4px;bottom:12px;line-height:1}
  .meta .hl{color:var(--pink)}
  .meta.left{left:17px}.meta.right{right:17px}

  .cover-photo{left:184px;top:-221px;width:372px;height:372px;border-radius:50%;background:linear-gradient(150deg,#ececed 0%,#d9d9db 55%,#4a4a4e 100%)}

  .footer{left:0;right:0;bottom:3px;height:9px}
  .footer .tab{position:absolute;left:0;top:0;width:4px;height:9px;background:var(--plum)}
  .footer .brand{position:absolute;left:6px;top:0;font-size:9px;color:var(--plum)}
  .footer .bar{position:absolute;left:37px;right:0;top:1px;height:8px;background:var(--plum);color:var(--white);font-size:5.6px;line-height:8px}
  .footer .site{position:absolute;left:0;right:37px;text-align:center}
  .footer .page{position:absolute;right:12px}

  .kicker{left:50%;width:17px;height:1.5px;margin-left:-8.5px;background:var(--pink)}
  .section-title{font-weight:700;font-size:13px;line-height:1;color:var(--ink)}
  .section-title .soft{color:var(--accent)}
  .tagline{font-size:4.6px;color:var(--muted);line-height:1}

  .toc-item{width:111px;height:9px;border-bottom:1px solid var(--rule);font-size:5.3px;font-weight:600;color:var(--ink);display:flex;justify-content:space-between;padding:0 1px}

  .vision-box{left:45px;top:59px;width:273px;height:95px;background:var(--plum);box-shadow:0 3px 8px rgba(40,20,50,.25);color:var(--white);font-size:8.4px;line-height:14.8px;text-align:center;display:flex;align-items:center;justify-content:center;padding:0 28px;font-weight:300}

  .mission{width:100px;margin-left:-50px;text-align:center}
  .mission h3{font-size:5.4px;font-weight:700;color:var(--ink)}
  .mission .dash{width:6px;height:1px;background:var(--pink);margin:4px auto 5px}
  .mission p{font-size:4.1px;line-height:6.4px;color:var(--muted)}
  .mission-card{left:136px;top:52px;width:92px;height:58px;background:var(--white);box-shadow:0 2px 6px rgba(40,20,50,.14)}

  .photo-office{left:38px;top:52px;width:97px;height:86px;background:linear-gradient(160deg,#c9d6dd 0%,#8fa5b3 50%,#3c5566 100%);box-shadow:0 2px 6px rgba(0,0,0,.2)}
  .body-copy{font-size:4.4px;line-height:7.4px;color:var(--muted)}
  .body-copy b{color:var(--ink)}

  .stat-tile{top:101px;height:36px;background:var(--white);box-shadow:0 2px 5px rgba(40,20,50,.16);text-align:center;padding-top:10px}
  .stat-tile.featured{top:100px;height:38px;background:var(--plum);color:var(--white);padding-top:11px}
  .stat-tile strong{display:block;font-size:9px;font-weight:600;line-height:1}
  .stat-tile span{display:block;font-size:4.3px;margin-top:4px}

  .figure{width:80px;margin-left:-40px;text-align:center}
  .figure strong{display:block;font-size:10px;font-weight:700;line-height:1}
  .figure .dash{width:4px;height:1px;background:var(--ink);margin:1px auto 3px}
  .figure span{font-size:5.4px}
</style>
</head>
<body>

<section class="slide col-1 row-1">
  <div class="photo-dark" role="img" aria-label="Dim overhead photo of a desk with a laptop and coffee cup"></div>
  <div class="brand center light" style="top:38px;font-size:24px">Norvel</div>
  <h1 class="title center light" style="top:91px">Presentation Title Goes Here</h1>
  <p class="subtitle center light" style="top:108px">Credential Subtitle Presentation</p>
  <p class="presenter center light" style="top:140px">Mr. Alan Brooke</p>
  <p class="meta left light">August <span class="hl">2023</span></p>
  <p class="meta right light">norvel.<span class="hl">site</span></p>
</section>

<section class="slide col-2 row-1">
  <div class="photo-dark keys" role="img" aria-label="Dark close-up photo of hands typing on a laptop"></div>
  <div class="brand light" style="left:19px;top:44px;font-size:20px">Norvel</div>
  <h1 class="title light" style="left:19px;top:85px">Presentation Title Goes Here</h1>
  <p class="subtitle light" style="left:19px;top:102px">Credential Subtitle Presentation</p>
  <p class="presenter light" style="left:19px;top:134px">Mr. Alan <span class="hl">Brooke</span></p>
  <p class="meta light" style="left:18px">August <span class="hl">2023</span></p>
</section>

<section class="slide col-3 row-1">
  <div class="brand center" style="top:38px;font-size:24px;color:var(--plum)">Norvel</div>
  <h1 class="title center" style="top:91px;color:#3a1d4a">Presentation Title Goes Here</h1>
  <p class="subtitle center" style="top:108px;color:var(--accent)">Credential Subtitle Presentation</p>
  <p class="presenter center" style="top:140px;color:var(--ink)">Mr. Alan Brooke</p>
  <p class="meta left">August <span class="hl">2023</span></p>
  <p class="meta right">norvel.<span class="hl">site</span></p>
</section>

<section class="slide col-1 row-2">
  <div class="cover-photo" role="img" aria-label="Overhead photo of a person working on a laptop at a white desk"></div>
  <div class="brand" style="left:17px;top:39px;font-size:20px;color:var(--plum)">Norvel</div>
  <h1 class="title" style="left:17px;top:91px">Presentation Title Goes Here</h1>
  <p class="subtitle" style="left:17px;top:108px">Credential Subtitle Presentation</p>
  <p class="presenter" style="left:17px;top:140px;color:#2a2450">Mr. Alan Brooke</p>
  <p class="meta left">August 2023</p>
  <p class="meta right">norvel.<span class="hl">site</span></p>
</section>

<section class="slide col-2 row-2">
  <div class="kicker" style="top:16px"></div>
  <h2 class="section-title center" style="top:23px">Presentation <span class="soft">List</span></h2>
  <p class="tagline center" style="top:39px">Here Our Subtitle</p>
  <div class="toc-item" style="left:48px;top:67px"><span>COVER SLIDES</span><span>01</span></div>
  <div class="toc-item" style="left:48px;top:93px"><span>PRESENTATION LIST</span><span>03</span></div>
  <div class="toc-item" style="left:48px;top:119px"><span>ABOUT US</span><span>04</span></div>
  <div class="toc-item" style="left:48px;top:146px"><span>OUR MISSIONS &amp; VISION</span><span>06</span></div>
  <div class="toc-item" style="left:206px;top:67px"><span>INFOGRAPH ONE</span><span>07</span></div>
  <div class="toc-item" style="left:206px;top:93px"><span>INFOGRAPH TWO</span><span>08</span></div>
  <div class="toc-item" style="left:206px;top:119px"><span>INFOGRAPH THREE</span><span>09</span></div>
  <div class="toc-item" style="left:206px;top:146px"><span>CLOSING SLIDES</span><span>10</span></div>
  <footer class="footer"><span class="tab"></span><span class="brand">Norvel</span><div class="bar"><span class="site">norvel.site</span><span class="page">page | 5</span></div></footer>
</section>

<section class="slide col-3 row-2">
  <div class="kicker" style="top:16px"></div>
  <h2 class="section-title center" style="top:24px">Our <span class="soft">Vision</span></h2>
  <p class="tagline center" style="top:40px">Here Our Subtitle</p>
  <div class="vision-box">Lorem ipsum dolor sit amet, consectetuer adipiscing elit. Maecenas porttitor congue massa. Fusce posuere, magna sed pulvinar ultricies, purus lectus malesuada libero.</div>
  <footer class="footer"><span class="tab"></span><span class="brand">Norvel</span><div class="bar"><span class="site">norvel.site</span><span class="page">page | 6</span></div></footer>
</section>

<section class="slide col-1 row-3">
  <div class="kicker" style="top:16px"></div>
  <h2 class="section-title center" style="top:22px">Our <span class="soft">Mission</span></h2>
  <div class="mission-card"></div>
  <div class="mission" style="left:71px;top:64px"><h3>Mission One</h3><div class="dash"></div><p>Lorem ipsum dolor sit amet,<br>consecter adipiscing eli Maecenas<br>porttitor adipiscing elit tam emotan.</p></div>
  <div class="mission" style="left:182px;top:64px"><h3>Mission Two</h3><div class="dash"></div><p>Lorem ipsum dolor sit amet,<br>consecter adipiscing eli Maecenas<br>porttitor adipiscing elit tam emotan.</p></div>
  <div class="mission" style="left:292px;top:64px"><h3>Mission Three</h3><div class="dash"></div><p>Lorem ipsum dolor sit amet,<br>consecter adipiscing eli Maecenas<br>porttitor adipiscing elit tam emotan.</p></div>
  <div class="mission" style="left:71px;top:127px"><h3>Mission Four</h3><div class="dash"></div><p>Lorem ipsum dolor sit amet,<br>consecter adipiscing eli Maecenas<br>porttitor adipiscing elit tam emotan.</p></div>
  <div class="mission" style="left:182px;top:127px"><h3>Mission Five</h3><div class="dash"></div><p>Lorem ipsum dolor sit amet,<br>consecter adipiscing eli Maecenas<br>porttitor adipiscing elit tam emotan.</p></div>
  <div class="mission" style="left:292px;top:127px"><h3>Mission Six</h3><div class="dash"></div><p>Lorem ipsum dolor sit amet,<br>consecter adipiscing eli Maecenas<br>porttitor adipiscing elit tam emotan.</p></div>
  <footer class="footer"><span class="tab"></span><span class="brand">Norvel</span><div class="bar"><span class="site">norvel.site</span><span class="page">page | 7</span></div></footer>
</section>

<section class="slide col-2 row-3">
  <div class="photo-office" role="img" aria-label="Photo of a man working on a laptop on a sofa beside a city window"></div>
  <div style="left:168px;top:51px;width:17px;height:1.5px;background:var(--pink)"></div>
  <h2 class="section-title" style="left:168px;top:59px">Think Legacy</h2>
  <p class="body-copy" style="left:168px;top:77px;width:160px">Lorem ipsum dolor sit amet, consectetuer adipiscing elit. Maecenas porttitor congue massa. Fusce posuere, magna sed pulvinar ultricies.</p>
  <div class="stat-tile" style="left:169px;width:34px"><strong>12+</strong><span>Partnership</span></div>
  <div class="stat-tile" style="left:241px;width:35px"><strong>120+</strong><span>Employee</span></div>
  <div class="stat-tile featured" style="left:202px;width:39px"><strong>400+</strong><span>Satisfy Cust</span></div>
  <footer class="footer"><span class="tab"></span><span class="brand">Norvel</span><div class="bar"><span class="site">norvel.site</span><span class="page">page | 8</span></div></footer>
</section>

<section class="slide col-3 row-3">
  <div class="kicker" style="top:21px"></div>
  <h2 class="section-title center" style="top:30px">Think Legacy</h2>
  <p class="tagline center" style="top:46px">Here Our Subtitle</p>
  <div class="kicker" style="top:71px;width:6px;margin-left:-3px"></div>
  <p class="body-copy center" style="top:79px;left:46px;right:40px;line-height:8px"><b>Lorem ipsum</b> dolor sit amet, consectetuer adipiscing elit. Maecenas porttitor congue massa. Fusce posuere, magna sed pulvinar ultricies, purus lectus malesuada libero, sit amet commodo magna eros quis urna.Nunc viverra imperdiet enim. Fusce est. Vivamus a tellus. Pellentesque habitant morbi tristique senectus et netus et malesuada.</p>
  <div class="figure" style="left:62px;top:134px"><strong>243</strong><div class="dash"></div><span>Project Done</span></div>
  <div class="figure" style="left:143px;top:134px"><strong>232</strong><div class="dash"></div><span>Satisfy Costumer</span></div>
  <div class="figure" style="left:224px;top:134px"><strong>37</strong><div class="dash"></div><span>Global Parthership</span></div>
  <div class="figure" style="left:303px;top:134px;width:90px;margin-left:-45px"><strong>32+</strong><div class="dash"></div><span>Certifications Company</span></div>
  <footer class="footer"><span class="tab"></span><span class="brand">Norvel</span><div class="bar"><span class="site">norvel.site</span><span class="page">page | 9</span></div></footer>
</section>

</body>
</html>
```